Core Value Graphic for a Service Disabled and Minority Certified contractor

My company, Keystone Aid Partners, is a US Federal Contractor that hires veterans and service disabled veterans. Our website is www.keystoneaid7.example. We work hard to maintain a 50:50 split between veterans and non-veterans on our team. Our tagline is "To Find a Better Way." We are continually looking to integrate technology and efficiency into all that we do.

I want a way to express our company core values visually so that our employees and customers alike can read them and get a sense of who we are, what drives us to succeed, and what makes up our team DNA.

I need an artist like you to help me represent our core values visually. In a manner that I can print it out on an 8"X11" sheet of paper or a large 48" X 48" poster, without losing the visual clarity or that it pixelates out of focus. I am looking for a color scheme that is patriotic with Red, White, and Blues and similar hues. I would also like to incorporate my logo and tagline into the design in some manner.

I have attached several examples of a Core Value Grids from other companies. I am hopeful it will inspire you, and a get your brain juices flowing to provide me with a knockout Core Value Grid that will rock only you can provide! I also include a copy of my company Core Values and a copy of our Logo.

Looking forward to seeing your creations. Thanks.

Target Market(s)

Employees, any potential strategic alliance partners, and customers.

Industry/Entity Type

Contractor

Requirements
Must have
• Patriotic feel and have my logo someplace on the document.

```html
<!DOCTYPE html>
<html lang="en">
<head>
<meta charset="utf-8">
<title>Keystone Aid Partners – Core Values</title>
<link rel="stylesheet" href="https://fonts.googleapis.com/css2?family=Roboto:wght@400;500;700&family=Varela+Round&family=Barlow+Semi+Condensed:wght@500&display=swap">
<style>
  :root{
    --stage:#cbcbcb;
    --paper:#f7f7f5;
    --navy:#002f5f;
    --green:#0a9a48;
    --orange:#e8761d;
    --teal:#3ab4c8;
    --magenta:#b54f8c;
    --purple:#6b5fa0;
    --ink:#333333;
    --red:#d3222a;
    --white:#ffffff;
  }
  *{margin:0;padding:0;box-sizing:border-box}
  html,body{width:1030px;height:1200px;overflow:hidden;background:var(--stage)}
  .poster{
    position:absolute;left:210px;top:168px;width:763px;height:1078px;
    background:var(--paper);transform:scale(0.8);transform-origin:0 0;
    font-family:"Roboto",Arial,sans-serif;
  }
  .masthead{position:absolute;left:0;top:0;width:763px;height:92px;background:var(--navy);overflow:hidden}
  .brand-tab{
    position:absolute;left:42px;top:7px;width:230px;height:85px;background:var(--white);
    border-radius:10px 10px 0 0;display:flex;align-items:center;gap:10px;padding-left:22px;
  }
  .brand-mark{width:14px;height:14px;background:var(--red);flex:none}
  .brand-name{font-weight:700;font-size:19px;line-height:21px;color:var(--navy);text-transform:uppercase}
  .masthead-title{
    position:absolute;left:420px;top:40px;font-family:"Barlow Semi Condensed",Arial,sans-serif;
    font-weight:500;font-size:58px;line-height:60px;color:var(--white);white-space:nowrap;
  }
  .tagline{
    position:absolute;left:0;top:130px;width:763px;text-align:center;
    font-weight:700;font-size:28px;letter-spacing:-0.5px;color:#111;
  }
  .value-card{
    position:absolute;left:38px;width:687px;border-radius:16px;padding:9px;
    display:flex;align-items:stretch;color:var(--white);
  }
  .value-card.reverse{flex-direction:row-reverse}
  .value-badge{
    width:212px;flex:none;background:var(--white);border-radius:10px 0 0 10px;
    display:flex;flex-direction:column;align-items:center;justify-content:center;
    font-family:"Varela Round",Arial,sans-serif;color:var(--ink);text-align:center;
  }
  .reverse .value-badge{border-radius:0 10px 10px 0}
  .value-copy{flex:1;padding:10px 10px 0 19px;font-size:10.5px;line-height:15px;text-align:justify}
  .reverse .value-copy{padding:10px 19px 0 9px}
  .value-copy p{margin-bottom:5px}
  .icon-slot{width:46px;height:40px;border-radius:8px;margin-bottom:6px}
  .badge-lead{font-size:18px;line-height:23px}
  .badge-key{font-size:27px;line-height:30px}

  .card-safety{top:178px;height:169px;background:var(--green)}
  .card-safety .badge-key{color:var(--green)}
  .card-safety .icon-slot{background:var(--green);border-radius:50%;width:44px;height:44px}
  .card-innovation{top:355px;height:168px;background:var(--orange)}
  .card-innovation .badge-lead{font-size:20px}
  .card-innovation .badge-key{color:var(--orange);font-size:32px;line-height:36px}
  .card-innovation .icon-slot{background:var(--red);width:60px;height:36px}
  .card-wingman{top:531px;height:169px;background:var(--teal)}
  .card-wingman .badge-key{color:var(--teal)}
  .card-wingman .icon-slot{background:#7a2a7e;width:44px;height:44px}
  .card-learning{top:708px;height:168px;background:var(--magenta)}
  .card-learning .badge-key{color:var(--magenta);font-size:26px}
  .card-learning .badge-lead{font-size:21px;line-height:30px}
  .card-learning .icon-slot{background:#e2256f;width:60px;height:44px;margin-bottom:14px}
  .card-leadership{top:884px;height:135px;background:var(--purple)}
  .card-leadership .value-copy{padding-top:6px}
  .card-leadership .icon-slot{background:#2f8f88;width:64px;height:34px;margin-bottom:0}
  .troops{font-size:37px;line-height:40px;color:var(--purple)}
  .troops-note{font-size:8px;line-height:9px}
  .card-leadership .badge-lead{font-size:20px;line-height:22px}

  .footer{
    position:absolute;left:0;top:1048px;width:763px;height:30px;background:var(--navy);
    color:var(--white);text-align:center;font-size:13px;line-height:30px;letter-spacing:6px;
  }
</style>
</head>
<body>
<main class="poster">
  <header class="masthead">
    <div class="brand-tab">
      <span class="brand-mark"></span>
      <span class="brand-name">Keystone Aid<br>Partners</span>
    </div>
    <h1 class="masthead-title">Core Values</h1>
  </header>

  <h2 class="tagline">TO FIND A BETTER WAY</h2>

  <section class="value-card card-safety">
    <div class="value-badge">
      <div class="icon-slot" role="img" aria-label="Tree inside circular arrows icon"></div>
      <div class="badge-lead">Everyone comes<br>back to the</div>
      <div class="badge-key">Green Zone</div>
    </div>
    <div class="value-copy">
      <p>WHAT IT MEANS - Safety takes precedence over every phase of the day's operation.</p>
      <p>HOW TO EXPRESS IT - Anyone can call a stop to the work in progress if an unsafe act is occurring. In fact, it is each team member's duty to do so, rectify the unsafe issue, then proceed. Never hesitate; everyone comes back. Finally, each After Action Review begins with discussing safety issues. We always let everyone on the team know of an unsafe situation, so it can be avoided in the future.</p>
      <p>RESULT - All team members go home to their loved ones each day to pursue their individual happiness.</p>
    </div>
  </section>

  <section class="value-card card-innovation reverse">
    <div class="value-badge">
      <div class="icon-slot" role="img" aria-label="Binoculars icon"></div>
      <div class="badge-lead">Boldly go.</div>
      <div class="badge-key">Seek. Find.</div>
    </div>
    <div class="value-copy">
      <p>WHAT IT MEANS: - We weave innovation into the fabric that makes up our company.</p>
      <p>HOW TO EXPRESS IT: - We're early adopters of technology. We quickly evaluate new technologies or processes that could separate us from our competition. Then we implement and evaluate these new technologies. We dump it quickly if we see it is not helping us achieve "Commander's Intent." We have the guts to be first. We iterate continuously and attack, attack, attack.</p>
      <p>RESULT: - We will be ahead of our competition. It' one mechanism that helps us scale. Prosperity favors the bold!</p>
    </div>
  </section>

  <section class="value-card card-wingman">
    <div class="value-badge">
      <div class="icon-slot" role="img" aria-label="Team member with laurel icon"></div>
      <div class="badge-lead">Never leave<br>your</div>
      <div class="badge-key">wingman</div>
    </div>
    <div class="value-copy">
      <p>WHAT IT MEANS We always help your team members be successful. Commitment to each other and to our own personal integrity is the fuel that empowers us.</p>
      <p>HOW TO EXPRESS IT If a Wingman is having challenges accomplishing their individual priorities or completing their assigned mission, volunteer to help them to do so.</p>
      <p>This goes for Subs/Suppliers as well. We help those who help us succeed! Always look to establish the best win-win relationship possible, and do what you can to support them if they get into a bind.</p>
      <p>RESULT Be there for them and they will be there for us.</p>
    </div>
  </section>

  <section class="value-card card-learning reverse">
    <div class="value-badge">
      <div class="icon-slot" role="img" aria-label="Open book icon"></div>
      <div class="badge-key">Fail Quackly</div>
      <div class="badge-lead">and learn</div>
    </div>
    <div class="value-copy">
      <p>WHAT IT MEANS If you're not making mistakes, you're not taking enough chances or getting out of your comfort zone.</p>
      <p>HOW TO EXPRESS IT Use your best judgment when trying something new. But, don't let your pride keep you from saying, "I was wrong" when your idea doesn't work. We trust you will know when it's time to dump the idea, or stop doing something that doesn't work.</p>
      <p>RESULT No one will ever be penalized for making a mistake. Don't be afraid to try something you believe will work. That's how we grow ourselves and our team</p>
    </div>
  </section>

  <section class="value-card card-leadership">
    <div class="value-badge">
      <div class="icon-slot" role="img" aria-label="Group of three team members icon"></div>
      <div class="troops">Troops</div>
      <div class="troops-note">(Team Members)</div>
      <div class="badge-lead">eat first</div>
    </div>
    <div class="value-copy">
      <p>WHAT IT MEANS No leader will put themselves ahead of their subordinates.</p>
      <p>HOW TO EXPRESS IT We lead by example. Demonstrate the moral courage and discipline to do the right thing at the highest level of quality.</p>
      <p>RESULT Every new teammember's will quickly realize their leaders genuinely care for their welfare and success This is the best way to drive Esprit de Corps and achieve excellence.</p>
    </div>
  </section>

  <footer class="footer">www.keystoneaid7.example</footer>
</main>
</body>
</html>
```